New Business Card Design Project

We require a business card design for Vexalund, a newly established Indian company.
Our focus is on the development, manufacturing, and export of a diverse array of pharmaceutical products on a global scale. The card should convey a professional appearance, as our primary markets are in Africa, China, and Southeast Asian nations.
We envision a two-sided business card, with the reverse side dedicated to a logo set against a solid color or an elegantly designed pattern. The corners should be rounded. We would appreciate seeing both horizontal and vertical design options. We trust the designer to utilize their expertise in creating this design.

The content for the business card is included in the attached Word file.

Target Market(s)

Our primary markets are in Africa, China, and Southeast Asian, Latin America, Maldives, Sri Lanka

Industry/Entity Type

Pharmaceutical Manufacturing and Export

Contact Information for Business Card

Colors

Designer to choose colors to be used in the design.

Requirements
Must have
• The reverse side of the business card features solely the logo along with the tagline, "Caring Every Day."
Should not have
• The logo should not exceed two instances, encompassing both the front and back sides of the card.

```html
<!DOCTYPE html>
<html lang="en">
<head>
<meta charset="utf-8">
<title>Vexalund Business Card</title>
<link rel="stylesheet" href="https://fonts.googleapis.com/css2?family=Arimo:wght@400;700&display=swap">
<style>
  :root {
    --stage: #2b2b2b;
    --card-white: #ffffff;
    --brand-blue: #29a8e0;
    --brand-coral: #f0604b;
    --tagline-grey: #555555;
    --on-blue: #ffffff;
  }
  * { box-sizing: border-box; margin: 0; padding: 0; }
  html, body {
    width: 1200px; height: 689px; overflow: hidden;
    background: var(--stage);
    font-family: "Arimo", Arial, sans-serif;
  }
  .stage {
    position: relative; width: 1200px; height: 689px;
    display: flex; align-items: center; justify-content: center; gap: 50px;
  }
  .card {
    width: 520px; height: 297px; border-radius: 22px;
    position: relative;
  }
  .card-back {
    background: var(--card-white);
    display: flex; flex-direction: column; align-items: center; justify-content: center;
  }
  .brand {
    display: flex; align-items: center; gap: 14px;
  }
  .brand-dot {
    width: 22px; height: 22px; border-radius: 50%;
    background: var(--brand-coral);
  }
  .brand-name {
    font-weight: 700; font-size: 50px; color: var(--brand-blue);
    letter-spacing: 1px;
  }
  .tagline {
    margin-top: 18px; font-size: 15px; color: var(--tagline-grey);
  }
  .card-front {
    background: var(--brand-blue); color: var(--on-blue);
    display: flex; align-items: center; justify-content: center; gap: 18px;
  }
  .person { text-align: right; }
  .person-name { font-weight: 700; font-size: 25px; letter-spacing: 0.5px; }
  .person-role { font-size: 13px; margin-top: 2px; }
  .person-email { font-size: 14px; margin-top: 4px; }
  .divider { width: 1px; height: 104px; background: var(--on-blue); opacity: 0.85; }
  .contact { font-size: 13px; line-height: 1.35; }
  .contact-address { margin-bottom: 10px; }
  .contact-row { display: flex; align-items: center; gap: 7px; }
  .contact-row svg { width: 12px; height: 12px; flex: none; }
</style>
</head>
<body>
<main class="stage">
  <section class="card card-back" aria-label="Card reverse">
    <div class="brand">
      <span class="brand-dot"></span>
      <span class="brand-name">Vexalund</span>
    </div>
    <p class="tagline">Caring Every Day</p>
  </section>

  <section class="card card-front" aria-label="Card front">
    <div class="person">
      <p class="person-name">Arvind K. Solanke</p>
      <p class="person-role">CEO</p>
      <p class="person-email">asolanke@vexalund.com</p>
    </div>
    <span class="divider"></span>
    <div class="contact">
      <p class="contact-address">12, Nilgiri Colony, Varanasi<br>221005, India</p>
      <p class="contact-row">
        <svg viewBox="0 0 24 24" aria-hidden="true"><path fill="#fff" d="M6.6 10.8a15.1 15.1 0 0 0 6.6 6.6l2.2-2.2a1 1 0 0 1 1-.25 11.4 11.4 0 0 0 3.6.57 1 1 0 0 1 1 1V20a1 1 0 0 1-1 1A17 17 0 0 1 3 4a1 1 0 0 1 1-1h3.5a1 1 0 0 1 1 1c0 1.25.2 2.45.57 3.57a1 1 0 0 1-.25 1z"/></svg>
        +919000012345
      </p>
      <p class="contact-row">
        <svg viewBox="0 0 24 24" aria-hidden="true"><circle cx="12" cy="12" r="10" fill="none" stroke="#fff" stroke-width="2.4"/><path d="M2 12h20M12 2c3 3 3 17 0 20M12 2c-3 3-3 17 0 20" fill="none" stroke="#fff" stroke-width="1.8"/></svg>
        www.vexalund.com
      </p>
    </div>
  </section>
</main>
</body>
</html>
```